Business Cards for new orthopaedic surgery practice

My husband and I are starting our own orthopaedic surgery practice. We are looking for a business card that is uniform, but one will have my name/title and the other will have his. You can just create one design with my name on it for now. But when I choose your design as the winning design I will ask that you add another copy with his name/title.

We are looking for classy, simple, elite all in one. We like dark blues/a little gold/yellow. Something that goes with our logo. We want our logo incorporated. Here is all the info you need:
Business name: RV Bone & Vitality Center
Location: 38517 North Willowmere Ave
Coral Springs, FL 33071
Phone: 954-218-4063
Fax: 954-582-7341
Email: info@myrvbonecare.example

Names: Lydia Vance, M.D.
Board Certified Hand and Upper Extremity Surgeon

Ebo Dansu, M.D.
Board Certified Hip & Knee Replacement/General Orthopaedic Surgeon

Can decide what you want to put on the back. Maybe a slogan:
Steady in Care. Centered on You

I am just going to upload our logo. The only thing is if we select you as the winning design, the location, and phone numbers may change. We will need your help to update that once fully solidified.

Industry/Entity Type

Medical

Contact Information for Business Card

Colors
0054AA
0677BA
7BADD7
CADEEF
E8F1F8
0094D4
00A9DD
6FCCEA
C7EBF8
E9F6FB

Requirements
Must have
• class, appeal,
Should not have
• We want to air on the side of masculine if we are looking at masculine vs. feminine feel. But we still want it classy, sophisticated, and something we will love

```html
<!DOCTYPE html>
<html lang="en">
<head>
<meta charset="utf-8">
<title>RV Bone &amp; Vitality Center – Business Card</title>
<link href="https://fonts.googleapis.com/css2?family=Montserrat:wght@400;500;600;700&display=swap" rel="stylesheet">
<style>
  :root {
    --page-bg: #e9ebef;
    --navy: #1b2a5e;
    --navy-deep: #142150;
    --navy-pattern: #1f3a8f;
    --gold: #c9a04a;
    --white: #ffffff;
  }
  * { box-sizing: border-box; margin: 0; padding: 0; }
  html, body { width: 1200px; height: 716px; overflow: hidden; }
  body {
    background: var(--page-bg);
    font-family: "Montserrat", sans-serif;
    position: relative;
  }
  .card {
    position: absolute;
    top: 203px;
    width: 540px;
    height: 309px;
    background: var(--navy);
    box-shadow: 0 8px 24px rgba(0,0,0,0.18);
    overflow: hidden;
  }
  .card--back { left: 40px; }
  .card--front { left: 620px; }

  .back-pattern {
    position: absolute; inset: 0;
    background: radial-gradient(circle at 50% 45%, var(--navy-pattern) 0%, var(--navy-deep) 80%);
  }
  .back-mark {
    position: absolute;
    left: 50%; top: 50%;
    transform: translate(-50%, -50%);
    display: flex; align-items: center; gap: 8px;
    background: var(--navy-deep);
    padding: 8px 14px;
    border-radius: 24px;
  }
  .back-mark__dot {
    width: 16px; height: 16px; border-radius: 50%;
    background: var(--white);
  }
  .back-mark__name {
    color: var(--white); font-size: 11px; font-weight: 600; letter-spacing: 0.5px;
  }

  .contact {
    position: absolute;
    left: 34px; top: 40px;
    color: var(--white);
    font-size: 12.5px;
    line-height: 1.3;
  }
  .contact__name {
    color: var(--gold); font-weight: 700; font-size: 19px; letter-spacing: 0.6px;
    text-transform: uppercase; margin-bottom: 4px;
  }
  .contact__title { margin-bottom: 10px; }
  .contact__address { margin-bottom: 8px; }
  .contact__list { list-style: none; }
  .contact__list li { display: flex; align-items: center; gap: 6px; }
  .contact__list svg { width: 11px; height: 11px; flex: none; }
  .contact__web .accent { color: var(--gold); }
  .contact__slogan {
    color: var(--gold); font-weight: 600; font-size: 13px; margin-top: 12px; letter-spacing: 0.3px;
  }

  .brand {
    position: absolute;
    right: 34px; top: 64px;
    width: 180px; height: 180px;
    border: 2px solid var(--gold);
    border-radius: 50%;
    display: flex; align-items: center; justify-content: center;
    text-align: center;
  }
  .brand__name {
    color: var(--white); font-weight: 600; font-size: 16px; letter-spacing: 1.5px;
    text-transform: uppercase; line-height: 1.4; padding: 0 18px;
  }
</style>
</head>
<body>
  <section class="card card--back" aria-label="Card back">
    <div class="back-pattern" role="img" aria-label="Tone-on-tone repeating pattern of the practice emblem on deep navy"></div>
    <div class="back-mark">
      <span class="back-mark__dot"></span>
      <span class="back-mark__name">RV Bone &amp; Vitality Center</span>
    </div>
  </section>

  <section class="card card--front" aria-label="Card front">
    <div class="contact">
      <p class="contact__name">Lydia Vance, M.D</p>
      <p class="contact__title">Board Certified Hand and<br>Upper Extremity Surgeon</p>
      <p class="contact__address">38517 North Willowmere Ave<br>Palm Hollow,FL 33490</p>
      <ul class="contact__list">
        <li><svg viewBox="0 0 24 24"><path fill="#c9a04a" d="M6.6 10.8a15 15 0 0 0 6.6 6.6l2.2-2.2c.3-.3.7-.4 1-.2 1.1.4 2.3.6 3.6.6.6 0 1 .4 1 1V20c0 .6-.4 1-1 1A17 17 0 0 1 3 4c0-.6.4-1 1-1h3.5c.6 0 1 .4 1 1 0 1.3.2 2.5.6 3.6.1.3 0 .7-.2 1z"/></svg>954-218-4063</li>
        <li><svg viewBox="0 0 24 24"><rect x="4" y="9" width="16" height="9" rx="1" fill="none" stroke="#c9a04a" stroke-width="2"/><rect x="7" y="4" width="10" height="5" fill="none" stroke="#c9a04a" stroke-width="2"/></svg>954-582-7341</li>
        <li><svg viewBox="0 0 24 24"><rect x="3" y="5" width="18" height="14" rx="1" fill="none" stroke="#c9a04a" stroke-width="2"/><path d="M3 6l9 7 9-7" fill="none" stroke="#c9a04a" stroke-width="2"/></svg>info@myrvbonecare.example</li>
        <li class="contact__web"><svg viewBox="0 0 24 24"><circle cx="12" cy="12" r="9" fill="none" stroke="#c9a04a" stroke-width="2"/><path d="M3 12h18M12 3c3 3 3 15 0 18M12 3c-3 3-3 15 0 18" fill="none" stroke="#c9a04a" stroke-width="1.5"/></svg><span>www.<span class="accent">myrvbonecare</span>.example</span></li>
      </ul>
      <p class="contact__slogan">Steady in Care. Centered on You</p>
    </div>
    <div class="brand">
      <p class="brand__name">RV Bone &amp; Vitality Center</p>
    </div>
  </section>
</body>
</html>
```